Rosko Tamblin

I am a songwriter and would like to include a bio, pictures, discography, CD covers and access to some of my music

Target Market(s)

Music Lovers, songwriters publishers

Coding

Coded - Design and coding required

Number of Pages Required

5+ page

Requirements
Must have
• Pictures of my CD covers, pictures of me and either my Music or links to my music
Nice to have
Should not have
• cartoons

```html
<!DOCTYPE html>
<html lang="en">
<head>
<meta charset="utf-8">
<title>Rosko Tamblin — Songwriter</title>
<link rel="stylesheet" href="https://fonts.googleapis.com/css2?family=Oswald:wght@500;700&family=Roboto:ital,wght@0,400;0,500;0,700;1,400&display=swap">
<style>
:root{
  --red:#ea1026;
  --white:#fff;
  --ink:#222;
  --muted:#666;
  --dark:#1d1d1f;
  --line:#555;
}
*{box-sizing:border-box;margin:0;padding:0}
html,body{width:1200px;height:2858px;overflow:hidden;background:#fff}
body{position:relative;font-family:'Roboto',sans-serif;color:var(--ink)}
.abs{position:absolute}
.display{font-family:'Oswald',sans-serif;font-weight:700;text-transform:uppercase;line-height:1.15}
a{color:inherit;text-decoration:none}

/* hero */
.hero{left:0;top:0;width:1200px;height:617px;background:radial-gradient(ellipse at 30% 65%,#e06a1a 0%,#9a2a0c 35%,#3a0d06 70%,#150403 100%)}
.hero-portrait{left:640px;top:40px;width:420px;height:577px;background:linear-gradient(180deg,#6b3a26,#2a1a14 60%,#1a1210)}
.hero-shade{left:0;top:0;width:1200px;height:617px;background:linear-gradient(90deg,rgba(0,0,0,.35),rgba(0,0,0,0) 55%),linear-gradient(180deg,rgba(0,0,0,.55),rgba(0,0,0,0) 25%)}
.logo{font-family:'Oswald',sans-serif;font-weight:700;color:var(--white);letter-spacing:1px;text-transform:uppercase}
.logo-top{left:111px;top:26px;font-size:24px;line-height:31px}
.nav{left:334px;top:50px;display:flex;gap:34px;font-size:14px;font-weight:500;color:var(--white)}
.nav .active{color:var(--red);position:relative}
.nav .active::after{content:"";position:absolute;left:0;right:0;top:30px;height:3px;background:var(--red)}
.social{left:977px;top:49px;display:flex;gap:14px}
.social span{width:16px;height:16px;border-radius:50%;background:var(--white)}
.hero-title{left:109px;top:192px;font-size:44px;line-height:52px;color:var(--white);letter-spacing:.5px}
.hero-text{left:111px;top:258px;width:520px;font-size:17px;line-height:26px;color:var(--white)}
.btn{display:flex;align-items:center;justify-content:center;background:var(--red);color:var(--white);border-radius:30px;font-weight:700}
.hero-btn{left:111px;top:335px;width:186px;height:55px;font-size:16px}
.thumb{top:440px;height:139px;display:flex;align-items:flex-end;justify-content:center;padding-bottom:28px;text-align:center;font-size:13.5px;line-height:25px;color:var(--white)}
.thumb.storm{left:111px;width:228px;background:linear-gradient(135deg,#4a4a58,#1d1d26)}
.thumb.fire{left:357px;width:233px;background:linear-gradient(135deg,#ff3a2a,#d8141d);border:2px solid var(--white);padding-bottom:18px}
.thumb.sea{left:609px;width:229px;background:linear-gradient(135deg,#2b3b45,#52666e 60%,#1e2a30)}
.thumb.colors{left:857px;width:230px;background:linear-gradient(135deg,#c3201e,#283c9a 35%,#e4c21a 65%,#1d7a3a)}

/* section titles */
.section-title{width:1200px;left:0;text-align:center;font-size:28px;line-height:36px;color:var(--ink)}
.section-title em{font-style:normal;color:var(--red)}

/* cd cards */
.cd-art{top:769px;height:204px;box-shadow:0 0 6px rgba(0,0,0,.2);border:1px solid #ddd}
.cd-art.child{left:111px;width:314px;background:linear-gradient(135deg,#f6efb8,#cfe1ef 50%,#eeeeee)}
.cd-art.banjo{left:443px;width:313px;background:linear-gradient(135deg,#28c05a,#e7b52a 40%,#d63a9b 75%,#5e7be2)}
.cd-art.pines{left:774px;width:314px;background:linear-gradient(135deg,#0c1a0a,#2a7a1c 50%,#0b0b0b)}
.date{top:987px;width:42px;height:42px;background:var(--red);color:var(--white);font-size:14px;line-height:17px;text-align:center;padding-top:4px}
.cd-title{top:983px;font-size:20px;line-height:26px;color:#333;white-space:nowrap}
.cd-text{top:1013px;width:248px;font-size:15.5px;line-height:25.5px;color:var(--muted)}
.cd-link{top:1097px;font-family:'Oswald',sans-serif;font-weight:500;font-size:13.5px;line-height:18px;color:var(--red);border-bottom:1px solid var(--red)}

/* reviews */
.reviews{left:0;top:1209px;width:1200px;height:472px;background:linear-gradient(90deg,#ee1c30,#e40f26 60%,#d80c22)}
.reviews .section-title{top:88px;color:var(--white)}
.quote{width:490px;color:var(--white)}
.quote .mark{font-family:Georgia,serif;font-size:36px;font-weight:700;line-height:20px;height:28px}
.quote p{font-style:italic;font-size:15.5px;line-height:26.6px}
.quote .name{font-family:'Oswald',sans-serif;font-weight:700;font-size:14px;margin-top:14px;text-transform:uppercase}
.quote .role{font-style:italic;font-size:14px}
.arrow{top:252px}

/* about */
.about-photo{left:111px;top:1840px;width:476px;height:319px;background:linear-gradient(135deg,#8a6a44,#a8875c 45%,#6d5236)}
.about-text{left:620px;top:1864px;width:467px;font-size:15.5px;line-height:25.7px;color:var(--muted);text-align:justify}
.about-btn{left:620px;top:2082px;width:162px;height:55px;font-size:16px}

/* footer */
.footer{left:0;top:2255px;width:1200px;height:603px;background:var(--dark);color:var(--white)}
.mail-title{left:0;top:70px;width:1200px;text-align:center;font-size:28px;line-height:36px}
.mail-box{left:211px;top:125px;width:777px;height:68px;background:var(--white);border-radius:3px}
.mail-box .field{left:58px;top:23px;font-size:17px;color:#666}
.mail-box .icon{left:26px;top:24px}
.subscribe{left:627px;top:12px;width:138px;height:46px;background:var(--red);color:var(--white);font-weight:700;font-size:16px;display:flex;align-items:center;justify-content:center;border-radius:2px}
.rule{height:1px;background:var(--line)}
.logo-foot{left:111px;top:250px;font-size:28px;line-height:40px}
.col-head{top:264px;font-size:17px;font-weight:500}
.col-head::after{content:"";display:block;width:24px;height:2px;background:var(--red);margin-top:7px}
.col-text{top:312px;font-size:13.5px;line-height:22px;color:#eee}
.follow{left:134px;top:345px;font-size:17px;font-weight:500}
.follow-list{left:134px;top:385px;display:flex;flex-direction:column;gap:10px;font-size:11px}
.follow-list li{list-style:none;display:flex;align-items:center;gap:10px;height:19px}
.follow-list li span{width:19px;height:19px;border-radius:50%;background:var(--white)}
.contact li{list-style:none;display:flex;gap:12px;margin-bottom:7px;font-size:13.5px;line-height:21px}
.contact svg{flex:none;margin-top:4px}
.foot-nav{left:352px;top:457px;width:736px;display:flex;justify-content:space-around;font-size:13px;font-weight:500}
.copy{left:0;top:517px;width:1200px;text-align:center;font-size:15px;color:#eee}
</style>
</head>
<body>

<header class="hero abs">
  <div class="hero-portrait abs" role="img" aria-label="Portrait of Rosko Tamblin smiling in front of a glowing fire crater at night"></div>
  <div class="hero-shade abs"></div>
  <div class="logo logo-top abs">Rosko<br>Tamblin</div>
  <nav class="nav abs">
    <a class="active">HOME</a><a>ABOUT US</a><a>DISCOGRAPHY</a><a>CD COVERS</a><a>REVIEWS</a><a>CONTACT US</a>
  </nav>
  <div class="social abs" aria-label="Social links"><span></span><span></span><span></span><span></span></div>
  <h1 class="hero-title display abs">Rosko Tamblin</h1>
  <p class="hero-text abs">Rosko Tamblin grew up in a small river town in the north. He began writing songs at the age of nine when his uncle .</p>
  <a class="btn hero-btn abs">GET STARTED</a>
  <div class="thumb storm display abs" role="img" aria-label="Album art: silhouette under a stormy lightning sky">Restless Seasons</div>
  <div class="thumb fire display abs" role="img" aria-label="Album art: flames over a red teacup">Combustible Heartland<br>30 Oct 2020</div>
  <div class="thumb sea display abs" role="img" aria-label="Album art: ship on a rough dark sea">When the Tide Turns</div>
  <div class="thumb colors display abs" role="img" aria-label="Album art: colourful abstract painting">Open Palms</div>
</header>

<section>
  <h2 class="section-title display abs" style="top:702px">My CD <em>Covers</em></h2>

  <div class="cd-art child abs" role="img" aria-label="CD cover, booklet and disc for Back When I Was Small"></div>
  <div class="date display abs" style="left:120px">Oct<br>30</div>
  <h3 class="cd-title display abs" style="left:178px">Back When I Was Small</h3>
  <p class="cd-text abs" style="left:178px">Lorem ipsum dolor sit amet, conse ctetur adipiscing elit, sed do eiusm od tempor incididunt.</p>
  <a class="cd-link abs" style="left:178px">Listen my music</a>

  <div class="cd-art banjo abs" role="img" aria-label="CD cover, booklet and disc for Porch Light Banjo"></div>
  <div class="date display abs" style="left:452px">Oct<br>30</div>
  <h3 class="cd-title display abs" style="left:509px">Porch Light Banjo</h3>
  <p class="cd-text abs" style="left:509px">Lorem ipsum dolor sit amet, conse ctetur adipiscing elit, sed do eiusm od tempor incididunt.</p>
  <a class="cd-link abs" style="left:509px">Listen my music</a>

  <div class="cd-art pines abs" role="img" aria-label="CD cover, booklet and disc for Pines Against the Sky"></div>
  <div class="date display abs" style="left:784px">Oct<br>30</div>
  <h3 class="cd-title display abs" style="left:842px">Pines Against the Sky</h3>
  <p class="cd-text abs" style="left:842px">Lorem ipsum dolor sit amet, conse ctetur adipiscing elit, sed do eiusm od tempor incididunt.</p>
  <a class="cd-link abs" style="left:842px">Listen my music</a>
</section>

<section class="reviews abs">
  <h2 class="section-title display abs">Our Cleint Reviews</h2>
  <div class="quote abs" style="left:93px;top:170px">
    <div class="mark">“</div>
    <p>At this point I have developed a continuous creative relationship with Rosko and have recorded on approximately 30 songs of his. He writes well-structured songs that allow me to flex my creative muscles. Rosko knows how to make his original ideas blossom into fully constructed arrangements that sound great.</p>
    <div class="name">Lucan Ferrety</div>
    <div class="role">Low Octave StudioBass</div>
  </div>
  <div class="quote abs" style="left:618px;top:170px">
    <div class="mark">“</div>
    <p>Rosko puts an all-star cast together to create crafted compositions. I'm glad to be a part of it. Rosko has a ton of great material and is producing it very well. Great music coming from Rosko. I have enjoyed all the projects I've worked on with him, He's producing a ton of great new music.</p>
    <div class="name">Oren Vasquel</div>
    <div class="role">Saxaphone</div>
  </div>
  <svg class="arrow abs" style="left:36px" width="16" height="48" viewBox="0 0 16 48"><path d="M14 2 L3 24 L14 46" fill="none" stroke="#fff" stroke-width="2"/></svg>
  <svg class="arrow abs" style="left:1148px" width="16" height="48" viewBox="0 0 16 48"><path d="M2 2 L13 24 L2 46" fill="none" stroke="#fff" stroke-width="2"/></svg>
</section>

<section>
  <h2 class="section-title display abs" style="top:1768px">About <em>Rosko Tamblin</em></h2>
  <div class="about-photo abs" role="img" aria-label="Photo of Rosko Tamblin in a white shirt outdoors by a mud-brick wall"></div>
  <p class="about-text abs">Rosko Tamblin grew up in a small river town in the north. He began writing songs at the age of nine when his uncle left an old upright piano in the family garage and never came back for it. His mother showed him a few simple chords on the piano and he was hooked. The following summer, they drove to a flea market across the state line and bought a secondhand guitar for $15. They fitted it with fresh steel strings and Tamblin began to teach himself how to play the guitar. He took evening lessons at a nearby music shop.</p>
  <a class="btn about-btn abs">Read More</a>
</section>

<footer class="footer abs">
  <h2 class="mail-title display abs">Join Our Mailing List for My Music</h2>
  <div class="mail-box abs">
    <svg class="icon abs" width="18" height="18" viewBox="0 0 18 18"><path d="M17 1 L1 8 L7 10 L9 17 Z M7 10 L17 1" fill="none" stroke="#333" stroke-width="1.6" stroke-linejoin="round"/></svg>
    <span class="field abs">Enter Email Address</span>
    <a class="subscribe abs">SUBSCRIBE</a>
  </div>
  <div class="rule abs" style="left:111px;top:228px;width:977px"></div>

  <div class="logo logo-foot abs">Rosko<br>Tamblin</div>
  <div class="follow abs">Follow Us</div>
  <ul class="follow-list abs">
    <li><span></span>Fanpage</li>
    <li><span></span>Snapgram</li>
    <li><span></span>Chirper</li>
    <li><span></span>Vidstream</li>
  </ul>

  <h4 class="col-head abs" style="left:358px">About Us</h4>
  <p class="col-text abs" style="left:358px;width:190px">Rosko Tamblin grew up in a small river town. He began writing songs at nine .</p>

  <h4 class="col-head abs" style="left:597px">My Music</h4>
  <p class="col-text abs" style="left:597px">Restless Seasons<br>When the Tide Turns<br>Back When I Was Small</p>

  <h4 class="col-head abs" style="left:815px">Contact Us</h4>
  <ul class="contact col-text abs" style="left:815px;width:240px">
    <li><svg width="10" height="13" viewBox="0 0 10 13"><path d="M5 0 A5 5 0 0 1 10 5 C10 8 5 13 5 13 C5 13 0 8 0 5 A5 5 0 0 1 5 0 Z" fill="#fff"/><circle cx="5" cy="5" r="2" fill="#1d1d1f"/></svg><span>123 Lorem ipsum dolor sit amet, consectetur adipiscing elit,</span></li>
    <li><svg width="11" height="11" viewBox="0 0 11 11"><path d="M2 0 L4 3 L3 4.5 C4 6.5 4.5 7 6.5 8 L8 7 L11 9 L9.5 11 C4 10.5 0.5 7 0 1.5 Z" fill="#fff"/></svg><span>123 456 7890</span></li>
    <li><svg width="12" height="9" viewBox="0 0 12 9"><rect width="12" height="9" fill="#fff"/><path d="M0 0 L6 5 L12 0" fill="none" stroke="#1d1d1f"/></svg><span>hello@roskotamblin.example</span></li>
  </ul>

  <div class="rule abs" style="left:352px;top:426px;width:736px"></div>
  <nav class="foot-nav abs">
    <a>HOME</a><span>|</span><a>ABOUT US</a><span>|</span><a>DISCOGRAPHY</a><span>|</span><a>CD COVERS</a><span>|</span><a>REVIEWS</a><span>|</span><a>CONTACT US</a>
  </nav>
  <div class="rule abs" style="left:352px;top:493px;width:736px"></div>
  <p class="copy abs">( C ) Copyrights 2020 Rosko Tamblin &nbsp;&nbsp;|&nbsp;&nbsp; All Rights Reserved</p>
</footer>

</body>
</html>
```